Salon and Spa Distributor Business Card

Need a business card. We are are distributor in the salon and spa industry. We identify with natural beauty. Need a card with:
Company Name: Petal Quarry"
Title: "President & CEO"
Address
Company Phone number
email
website
Tag Line:" The Professional Salon Source"

Industry/Entity Type

Business

Contact Information for Business Card

Name: Dov Strommen
Title: "President & CEO"
Address: 31 Harlow Ln, Bexmoor, NJ 07813
Company Phone number: 800-463-5918
email: dovstrommen@petalquarry.example
website: www.petalquarry.example

Requirements
Should not have
• No black backgrounds

```html
<!DOCTYPE html>
<html lang="en">
<head>
<meta charset="utf-8">
<title>Petal Quarry Business Card</title>
<link rel="stylesheet" href="https://fonts.googleapis.com/css2?family=Open+Sans:ital,wght@0,400;0,700;1,400&display=swap">
<style>
  :root {
    --page-bg: #e6e6e6;
    --green-deep: #005a28;
    --green-mid: #1a7a36;
    --green-soft: #3a8a44;
    --green-bright: #3fae3a;
    --green-light: #6cc24a;
    --card-white: #f7f7f7;
    --ink: #3a3a3a;
    --white: #ffffff;
  }
  * { margin: 0; padding: 0; box-sizing: border-box; }
  html, body { width: 1200px; height: 576px; overflow: hidden; }
  body {
    background: var(--page-bg);
    font-family: "Open Sans", Arial, sans-serif;
    position: relative;
  }
  .card {
    position: absolute;
    border-radius: 14px;
    overflow: hidden;
    box-shadow: 0 3px 6px rgba(0,0,0,0.18);
  }
  .card-front {
    left: 82px; top: 139px; width: 484px; height: 293px;
    background: linear-gradient(180deg, var(--green-deep) 0%, var(--green-mid) 55%, var(--green-soft) 100%);
    color: var(--white);
    display: flex; flex-direction: column; align-items: center; justify-content: center;
  }
  .front-mark {
    width: 62px; height: 62px; border-radius: 50%;
    background: var(--white);
    margin-bottom: 22px; margin-top: 6px;
  }
  .front-name { font-size: 27px; font-weight: 400; letter-spacing: 0.2px; }

  .card-back {
    left: 602px; top: 138px; width: 480px; height: 291px;
    background: var(--card-white);
  }
  .back-waves { position: absolute; left: 0; top: 0; width: 480px; height: 291px; }
  .holder { position: absolute; left: 23px; top: 46px; }
  .holder-name { font-size: 18px; font-weight: 700; color: var(--green-deep); line-height: 1.2; }
  .holder-title { font-size: 10.5px; color: var(--ink); margin-top: 2px; }

  .wordmark {
    position: absolute; right: 24px; top: 38px;
    display: flex; align-items: center; gap: 10px;
  }
  .wordmark-dot { width: 40px; height: 40px; border-radius: 50%; background: var(--green-bright); }
  .wordmark-name {
    font-size: 28px; line-height: 1.0; color: var(--green-bright); font-weight: 400;
  }

  .contact { position: absolute; left: 23px; top: 143px; list-style: none; }
  .contact li {
    font-size: 12.5px; color: var(--ink); height: 18px;
    display: flex; align-items: center; gap: 8px;
  }
  .contact svg { width: 11px; height: 11px; fill: var(--green-deep); flex: none; }
  .contact .address { margin-top: 3px; }

  .tagline {
    position: absolute; right: 26px; bottom: 28px;
    color: var(--white); font-style: italic; font-size: 12.5px;
    text-align: right; line-height: 1.45;
  }
</style>
</head>
<body>
  <div class="card card-front">
    <div class="front-mark"></div>
    <div class="front-name">Petal Quarry</div>
  </div>

  <div class="card card-back">
    <svg class="back-waves" viewBox="0 0 600 364" preserveAspectRatio="none" aria-hidden="true">
      <path d="M0,300 C120,330 330,318 600,198 L600,208 C340,332 140,346 0,318 Z" fill="var(--green-bright)"/>
      <path d="M0,322 C150,356 360,330 600,218 L600,364 L0,364 Z" fill="var(--green-deep)"/>
      <path d="M0,318 C90,342 230,350 420,296 C260,352 110,354 0,334 Z" fill="var(--green-light)"/>
    </svg>

    <div class="holder">
      <div class="holder-name">Petal Quarry</div>
      <div class="holder-title">President &amp; CEO</div>
    </div>

    <div class="wordmark">
      <div class="wordmark-dot"></div>
      <div class="wordmark-name">Petal<br>Quarry</div>
    </div>

    <ul class="contact">
      <li>
        <svg viewBox="0 0 24 24"><path d="M3 9c0-3 4-5 9-5s9 2 9 5v2h-5V9H8v2H3zM6 12h12l2 8H4z"/></svg>
        800-463-5918
      </li>
      <li>
        <svg viewBox="0 0 24 24"><path d="M2 5h20v14H2zM4 7v1l8 5 8-5V7l-8 5z"/></svg>
        dovstrommen@petalquarry.example
      </li>
      <li>
        <svg viewBox="0 0 24 24"><path d="M12 2a10 10 0 1 0 0 20a10 10 0 1 0 0-20zM4 11h4c0-2.5.6-5 1.6-6.6A8 8 0 0 0 4 11zm6 0h4c0-2.8-.8-5.4-2-6.8-1.2 1.4-2 4-2 6.8zm6 0h4a8 8 0 0 0-5.6-6.6c1 1.6 1.6 4.1 1.6 6.6zM4 13a8 8 0 0 0 5.6 6.6C8.6 18 8 15.5 8 13zm6 0c0 2.8.8 5.4 2 6.8 1.2-1.4 2-4 2-6.8zm6 0c0 2.5-.6 5-1.6 6.6A8 8 0 0 0 20 13z"/></svg>
        www.petalquarry.example
      </li>
      <li class="address">31 Harlow Ln, Bexmoor, NJ 07813</li>
    </ul>

    <div class="tagline">The Professional<br>Salon Source</div>
  </div>
</body>
</html>
```